Brightfield Ventures Inc. Letterhead

Creation of attractive and eye catching letterhead for a business start-up for the construction industry. Letterhead must relate to construction, but avoid standard hammer and tools in the design.

I forgot to add some details, sorry about that. Some pertinent info: Ph: 916-555-0187 brightfieldventures.example 448 Willowmere Ave, Ste 210 Folsom, CA 95999 info@brightfieldventures.example not sure if slogan should be in there" “Connecting construction professionals to create a purpose driven industry.” must be able to be used in word. Thanks!

```html
<!DOCTYPE html>
<html lang="en">
<head>
<meta charset="utf-8">
<title>Brightfield Ventures Inc. Letterhead</title>
<link rel="stylesheet" href="https://fonts.googleapis.com/css2?family=Lato:wght@400;700&family=Yellowtail&display=swap">
<style>
  :root {
    --navy: #1d1f5b;
    --red: #c11f27;
    --ink: #4b4b4b;
    --rule: #b9b9b9;
    --paper: #ffffff;
  }
  * { margin: 0; padding: 0; box-sizing: border-box; }
  html, body { width: 921px; height: 1200px; overflow: hidden; background: var(--paper); }
  .letterhead {
    position: relative;
    width: 921px;
    height: 1200px;
    background: var(--paper);
    font-family: "Lato", sans-serif;
    color: var(--ink);
  }
  .brand {
    position: absolute;
    left: 66px;
    top: 62px;
    width: 300px;
  }
  .brand-title { display: flex; align-items: center; gap: 10px; }
  .brand-mark { width: 16px; height: 16px; background: var(--red); flex: none; }
  .brand-name {
    font-weight: 700;
    font-size: 23px;
    color: var(--navy);
    letter-spacing: 0.3px;
    white-space: nowrap;
  }
  .brand-rule {
    height: 2px;
    background: var(--red);
    margin: 10px 0 8px;
    width: 286px;
  }
  .brand-slogan {
    font-size: 11.5px;
    line-height: 15px;
    color: var(--navy);
    width: 286px;
  }
  .contact {
    position: absolute;
    left: 646px;
    top: 56px;
    height: 58px;
    border-left: 1px solid var(--rule);
    padding-left: 12px;
    font-size: 13.5px;
    line-height: 19.5px;
    color: #444;
  }
  .contact-row { display: flex; align-items: center; gap: 5px; white-space: nowrap; }
  .contact-row svg { width: 10px; height: 10px; flex: none; }
  .salutation {
    position: absolute;
    left: 68px;
    top: 330px;
    font-weight: 700;
    font-size: 17px;
    color: var(--navy);
  }
  .body-copy {
    position: absolute;
    left: 68px;
    width: 786px;
    font-size: 17.7px;
    line-height: 27.7px;
  }
  .body-copy .line { display: block; text-align: justify; text-align-last: justify; white-space: nowrap; }
  .body-copy .line.last { text-align-last: left; }
  .p1 { top: 375px; }
  .p2 { top: 534px; }
  .p3 { top: 691px; }
  .closing {
    position: absolute;
    left: 70px;
    top: 861px;
    font-size: 20px;
    color: #222;
  }
  .signature {
    position: absolute;
    left: 70px;
    top: 893px;
    font-family: "Yellowtail", "Brush Script MT", cursive;
    font-size: 38px;
    color: var(--navy);
  }
  .footer-wave { position: absolute; left: 0; top: 1060px; width: 921px; height: 140px; }
  .address {
    position: absolute;
    left: 0;
    width: 921px;
    top: 1168px;
    display: flex;
    justify-content: center;
    align-items: center;
    gap: 5px;
    font-size: 13.5px;
    color: #fff;
  }
  .address svg { width: 10px; height: 12px; }
</style>
</head>
<body>
<div class="letterhead">
  <div class="brand">
    <div class="brand-title">
      <span class="brand-mark"></span>
      <span class="brand-name">Brightfield Ventures Inc.</span>
    </div>
    <div class="brand-rule"></div>
    <p class="brand-slogan">Connecting construction professionals to create a purpose driven industry.</p>
  </div>

  <div class="contact">
    <div class="contact-row">
      <svg viewBox="0 0 10 10"><circle cx="5" cy="5" r="4.3" fill="none" stroke="#c11f27" stroke-width="1"/><path d="M3.6 2.8 L4.6 4.2 L4 4.8 Q4.6 6 5.4 6.4 L6 5.8 L7.2 6.6 L6.6 7.4 Q4 7 2.8 3.6Z" fill="#c11f27"/></svg>
      <span>Ph: 916-555-0187</span>
    </div>
    <div class="contact-row">
      <svg viewBox="0 0 10 10"><rect x="1" y="3" width="8" height="5.5" fill="#c11f27"/><path d="M1 3 L5 6 L9 3" fill="none" stroke="#fff" stroke-width="0.8"/></svg>
      <span>info@brightfieldventures.example</span>
    </div>
    <div class="contact-row">
      <svg viewBox="0 0 10 10"><circle cx="5" cy="5" r="4.2" fill="none" stroke="#c11f27" stroke-width="1"/><ellipse cx="5" cy="5" rx="1.8" ry="4.2" fill="none" stroke="#c11f27" stroke-width="0.8"/><line x1="0.8" y1="5" x2="9.2" y2="5" stroke="#c11f27" stroke-width="0.8"/></svg>
      <span>brightfieldventures.example</span>
    </div>
  </div>

  <p class="salutation">Dear Mr. Lorem,</p>

  <p class="body-copy p1">
    <span class="line">Lorem ipsum dolor sit amet, consectetuer adipiscing elit, sed diam nonummy nibh euismod tinci-</span>
    <span class="line">dunt ut laoreet dolore magna aliquam erat volutpat. Ut wisi enim ad minim veniam, quis nostrud</span>
    <span class="line">exerci tation ullamcorper suscipit lobortis nisl ut aliquip ex ea commodo consequat. Duis autem vel</span>
    <span class="line">eum iriure dolor in hendiusto odio dignissim qui blandit praesent luptatum zzril delenit augue duis</span>
    <span class="line last">dolore te feugait nulla facilisi.</span>
  </p>
  <p class="body-copy p2">
    <span class="line">Lorem ipsum dolor sit amet, consectetuer adipiscing elit, sed diam nonummy nibh euismod tinci-</span>
    <span class="line">dunt ut laoreet dolore magna aliquam erat volutpat. Ut wisi enim ad minim veniam, quis nostrud</span>
    <span class="line">exerci tation ullamcorper suscipit lobortis nisl ut aliquip ex ea commodo consequat. Duis autem vel</span>
    <span class="line">eum iriure dolor in hendiusto odio dignissim qui blandit praesent luptatum zzril delenit augue duis</span>
    <span class="line last">dolore te feugait nulla facilisi.</span>
  </p>
  <p class="body-copy p3">
    <span class="line">Lorem ipsum dolor sit amet, consectetuer adipiscing elit, sed diam nonummy nibh euismod tinci-</span>
    <span class="line">dunt ut laoreet dolore magna aliquam erat volutpat. Ut wisi enim ad minim veniam, quis nostrud</span>
    <span class="line">exerci tation ullamcorper suscipit lobortis nisl ut aliquip ex ea commodo consequat. Duis autem vel</span>
    <span class="line">eum iriure dolor in hendiusto odio dignissim qui blandit praesent luptatum zzril delenit augue duis</span>
    <span class="line last">dolore te feugait nulla facilisi.</span>
  </p>

  <p class="closing">Sincerely Your,</p>
  <p class="signature">Your Name</p>

  <svg class="footer-wave" viewBox="0 0 921 140" preserveAspectRatio="none" aria-hidden="true">
    <path d="M0 16 C 110 70, 300 84, 540 82 C 700 80, 840 84, 921 112 L921 140 L0 140 Z" fill="var(--red)"/>
    <path d="M0 66 C 150 104, 380 98, 600 90 C 740 86, 860 94, 921 116 L921 140 L0 140 Z" fill="var(--navy)" stroke="#fff" stroke-width="4"/>
  </svg>
  <p class="address">
    <svg viewBox="0 0 10 12"><path d="M5 11.5 C 2 7.5 1 6 1 4.2 A4 4 0 0 1 9 4.2 C 9 6 8 7.5 5 11.5Z" fill="#fff"/><circle cx="5" cy="4.2" r="1.5" fill="var(--navy)"/></svg>
    <span>448 Willowmere Ave, Ste 210, Folsom, CA 95999</span>
  </p>
</div>
</body>
</html>
```